Dietitian needs awesome business card

I need a contemporary design that's eye catching but professional.
My card is to given to doctors, specialists and patients alike.
I manage patients with chronic diseases
I have uploaded my logo and current business card, I would also like the other Certified Clinical Nutritionist logo incorporated into the design

Target Market(s)

Doctors, specialists and patients

Industry/Entity Type

Healthcare

Contact Information for Business Card

www.brightfieldnutrition.com.au
Ph: 0427 561 903
Fax: 6457 2183
email: marcus.k.diet@fernmail.com
Space on the back of the card with: Appointment date, Appointment time and appointment location

Font styles to use
Serif

Colors
fbee3e
876aae
ffc214

Requirements
Must have
• My Logo
• Certified Clinical Nutritionist Logo
• My 4 locations - Pinebrook Medical Centre, North Corrin Health, Hollis Medical, Ashcombe Doctors Surgery
Nice to have
• I like the colours in my current business card

```html
<!DOCTYPE html>
<html lang="en">
<head>
<meta charset="utf-8">
<title>Brightfield Nutrition &amp; Dietetics – Business Card</title>
<link href="https://fonts.googleapis.com/css2?family=Lora:ital,wght@0,400;0,600;1,400&display=swap" rel="stylesheet">
<style>
  :root {
    --stage: #2b2b2b;
    --navy: #1f3a93;
    --blue: #1565c0;
    --green: #7ab929;
    --orange: #f47b20;
    --ink: #444;
    --muted: #6b7380;
    --rule: #cfcfcf;
    --back-bg: #edf6e0;
    --white: #ffffff;
  }
  * { margin: 0; padding: 0; box-sizing: border-box; }
  html, body { width: 1200px; height: 987px; overflow: hidden; }
  body { background: var(--stage); font-family: "Lora", serif; position: relative; }

  .card { position: absolute; left: 293px; width: 615px; height: 352px; overflow: hidden; }
  .card--front { top: 130px; background: var(--white); }
  .card--back { top: 505px; background: var(--back-bg); }

  .brand { position: absolute; right: 36px; top: 36px; display: flex; align-items: center; gap: 12px; }
  .brand__dot { width: 60px; height: 60px; border-radius: 50%; background: var(--green); flex: none; }
  .brand__name { color: var(--navy); font-weight: 400; line-height: 1.1; }
  .brand__line1 { display: block; font-size: 36px; }
  .brand__line2 { display: block; font-size: 15px; }

  .person { position: absolute; left: 26px; top: 166px; }
  .person__name { font-size: 22px; font-weight: 600; color: var(--navy); line-height: 1.25; }
  .person__role { font-size: 16px; color: var(--green); margin-top: 2px; }

  .badge { position: absolute; left: 507px; top: 182px; width: 74px; height: 35px; background: var(--orange); border-radius: 2px; }

  .divider { position: absolute; left: 26px; right: 34px; top: 225px; height: 1px; background: var(--rule); }

  .contacts { position: absolute; left: 26px; top: 238px; list-style: none; }
  .contacts li { display: flex; align-items: center; gap: 8px; font-size: 15px; color: var(--ink); height: 23.5px; }
  .contacts svg { width: 16px; height: 16px; fill: var(--navy); flex: none; }

  .locations { position: absolute; right: 34px; top: 236px; list-style: none; text-align: right; }
  .locations li { font-size: 12px; color: var(--muted); line-height: 17px; }
  .locations li::after { content: ""; display: inline-block; width: 6px; height: 6px; border-radius: 50%; background: var(--green); margin-left: 6px; vertical-align: middle; }

  .footer-band { position: absolute; left: 0; bottom: 0; width: 615px; height: 42px; }
  .footer-band svg { display: block; }
  .footer-band__url { position: absolute; right: 24px; bottom: 11px; color: var(--white); font-size: 16px; font-style: italic; }

  .back-title { position: absolute; top: 30px; left: 0; width: 100%; text-align: center; color: var(--navy); font-weight: 400; line-height: 1.1; }
  .back-title__line1 { display: block; font-size: 56px; }
  .back-title__line2 { display: block; font-size: 27px; }

  .field { position: absolute; display: flex; align-items: flex-end; color: var(--navy); font-size: 17px; }
  .field__line { flex: 1; border-bottom: 1px solid #8a98a8; margin: 0 4px 5px 6px; }
  .field__suffix { font-size: 13px; margin-bottom: 1px; }
  .field--date { left: 37px; top: 180px; width: 267px; }
  .field--time { left: 342px; top: 180px; width: 236px; }
  .field--location { left: 37px; top: 236px; width: 541px; }

  .back-url { position: absolute; top: 292px; left: 0; width: 100%; text-align: center; color: var(--navy); font-size: 16px; font-style: italic; letter-spacing: 0.3em; }
</style>
</head>
<body>

<section class="card card--front">
  <div class="brand">
    <span class="brand__dot"></span>
    <span class="brand__name">
      <span class="brand__line1">Brightfield</span>
      <span class="brand__line2">Nutrition &amp; Dietetics</span>
    </span>
  </div>

  <div class="person">
    <h1 class="person__name">Marcus Kellerman</h1>
    <p class="person__role">Nutritionist &amp; Chef</p>
  </div>

  <div class="badge" role="img" aria-label="Certified Clinical Nutritionist badge"></div>
  <div class="divider"></div>

  <ul class="contacts">
    <li>
      <svg viewBox="0 0 24 24" aria-hidden="true"><path d="M6.6 10.8a15.1 15.1 0 0 0 6.6 6.6l2.2-2.2c.3-.3.7-.4 1-.2 1.1.4 2.3.6 3.6.6.6 0 1 .4 1 1V20c0 .6-.4 1-1 1A17 17 0 0 1 3 4c0-.6.4-1 1-1h3.5c.6 0 1 .4 1 1 0 1.3.2 2.5.6 3.6.1.3 0 .7-.2 1z"/></svg>
      0427 561 903
    </li>
    <li>
      <svg viewBox="0 0 24 24" aria-hidden="true"><path d="M7 3h10v4H7zM4 8h16a2 2 0 0 1 2 2v6h-4v4H6v-4H2v-6a2 2 0 0 1 2-2zm4 7v3h8v-3z"/></svg>
      6457 2183
    </li>
    <li>
      <svg viewBox="0 0 24 24" aria-hidden="true"><path d="M3 5h18v14H3zm2 2v.5l7 4.5 7-4.5V7zm0 2.8V17h14V9.8l-7 4.5z"/></svg>
      marcus.k.diet@fernmail.com
    </li>
  </ul>

  <ul class="locations">
    <li>Pinebrook Medical Centre</li>
    <li>North Corrin Health</li>
    <li>Hollis Medical</li>
    <li>Ashcombe Doctors Surgery</li>
  </ul>

  <div class="footer-band">
    <svg width="615" height="42" viewBox="0 0 615 42" aria-hidden="true">
      <defs>
        <linearGradient id="stripe-green" x1="0" x2="1">
          <stop offset="0" stop-color="#6bb52c"/>
          <stop offset="1" stop-color="#b5d22c"/>
        </linearGradient>
        <linearGradient id="stripe-blue" x1="0" x2="1">
          <stop offset="0" stop-color="#1f9ad6"/>
          <stop offset="1" stop-color="#1e2f8f"/>
        </linearGradient>
      </defs>
      <rect x="0" y="17" width="370" height="10" fill="url(#stripe-green)"/>
      <rect x="0" y="27" width="615" height="15" fill="url(#stripe-blue)"/>
      <polygon points="380,0 615,0 615,42 352,42" fill="url(#stripe-blue)"/>
    </svg>
    <span class="footer-band__url">brightfieldnutrition.com.au</span>
  </div>
</section>

<section class="card card--back">
  <h2 class="back-title">
    <span class="back-title__line1">Brightfield</span>
    <span class="back-title__line2">Nutrition &amp; Dietetics</span>
  </h2>

  <div class="field field--date">Date :<span class="field__line"></span></div>
  <div class="field field--time">Time :<span class="field__line"></span><span class="field__suffix">AM/PM</span></div>
  <div class="field field--location">Location :<span class="field__line"></span></div>

  <p class="back-url">brightfieldnutrition.com.au</p>
</section>

</body>
</html>
```